Corporate Business Card

Very professional, Modern, Not to busy, include phone address email, website
(253) 617-4930, 18761 52nd Avenue S, Kent, WA 98047, martin@plumlinegroup.com, varkoworks.com

Target Market(s)

Manufacturing

Industry/Entity Type

Aero, machining, manufacturing, Off road racing

Contact Information for Business Card

Phone, address email, website

```html
<!DOCTYPE html>
<html lang="en">
<head>
<meta charset="utf-8">
<title>Varko Works – Business Card</title>
<link href="https://fonts.googleapis.com/css2?family=Montserrat:wght@400;500;700;800&display=swap" rel="stylesheet">
<style>
  :root {
    --navy: #14336e;
    --ink: #1c1c1c;
    --card: #ffffff;
    --backdrop: #d8d1c1;
  }
  html, body {
    margin: 0;
    padding: 0;
    width: 1116px;
    height: 1200px;
    overflow: hidden;
    background: var(--backdrop);
    font-family: "Montserrat", sans-serif;
  }
  .canvas {
    position: relative;
    width: 1116px;
    height: 1200px;
  }
  .card {
    position: absolute;
    left: 224px;
    width: 669px;
    height: 384px;
    background: var(--card);
    border-radius: 28px;
    overflow: hidden;
  }
  .card-front { top: 177px; }
  .card-back { top: 639px; }

  .wordmark {
    position: absolute;
    left: 0;
    right: 0;
    text-align: center;
    color: var(--navy);
    font-weight: 800;
    letter-spacing: 1px;
    white-space: nowrap;
  }
  .card-front .wordmark { top: 52px; font-size: 48px; line-height: 60px; }
  .card-back .wordmark { top: 153px; font-size: 62px; line-height: 78px; }

  .holder {
    position: absolute;
    top: 199px;
    left: 0;
    right: 0;
    text-align: center;
  }
  .holder-name {
    color: var(--navy);
    font-weight: 700;
    font-size: 25px;
    line-height: 30px;
    letter-spacing: 0.3px;
  }
  .holder-title {
    color: var(--ink);
    font-size: 16px;
    line-height: 22px;
    margin-top: 2px;
  }

  .address {
    position: absolute;
    top: 296px;
    right: 358px;
    text-align: right;
    color: var(--ink);
    font-size: 16px;
    line-height: 26px;
    white-space: nowrap;
  }
  .divider {
    position: absolute;
    left: 334px;
    top: 279px;
    width: 2px;
    height: 70px;
    background: var(--navy);
  }
  .contacts {
    position: absolute;
    left: 350px;
    top: 275px;
    margin: 0;
    padding: 0;
    list-style: none;
    color: var(--ink);
    font-size: 16px;
    line-height: 25px;
    white-space: nowrap;
  }
  .contacts li {
    display: flex;
    align-items: center;
    gap: 4px;
  }
  .contacts svg {
    width: 14px;
    height: 14px;
    fill: var(--navy);
    flex: none;
  }
</style>
</head>
<body>
<main class="canvas">
  <section class="card card-front">
    <div class="wordmark">VARKO WORKS</div>
    <div class="holder">
      <div class="holder-name">DANIEL HALE</div>
      <div class="holder-title">Owner/CEO</div>
    </div>
    <div class="address">18761 52nd Avenue<br>S, Kent, WA 98047</div>
    <div class="divider"></div>
    <ul class="contacts">
      <li>
        <svg viewBox="0 0 16 16" aria-hidden="true"><path d="M3.6 1.2l2.3 2.6-1.3 1.9c.9 2 2.6 3.7 4.6 4.6l1.9-1.3 2.6 2.3-1.4 2.4C7 13.5 2.5 9 1.2 3z"/></svg>
        (253) 617-4930
      </li>
      <li>
        <svg viewBox="0 0 16 16" aria-hidden="true"><path d="M1.5 4h13v1L8 9 1.5 5zM1.5 6.3L8 10.3l6.5-4V12h-13z"/></svg>
        martin@plumlinegroup.com
      </li>
      <li>
        <svg viewBox="0 0 16 16" aria-hidden="true"><circle cx="8" cy="8" r="6.5"/><path d="M5 5.5l2 .5 1 2-1.5 1 .5 2.5-2-1.5-.5-2.5zM9.5 4l2 1 .5 2.5-1.5-.5z" fill="#fff"/></svg>
        www.varkoworks.com
      </li>
    </ul>
  </section>

  <section class="card card-back">
    <div class="wordmark">VARKO WORKS</div>
  </section>
</main>
</body>
</html>
```